Tidal Forge - Crypto Currency Miner Powered by Renewable Energy Website

We Need Web Pages Design for Website for Crypto Currency Miner

Serivices include:
Mining Rig Sales
Housing for Rigs turnkey on renewable energy grid
Cloud Mining term packages
Updates

http://www.vaultrigsurvey.example (Competitors sites)

Target Market(s)

Investers for Mining Rigs and terms for 1,2 or 3 years of Hash rate

Industry/Entity Type

Mining

Number of Pages Required

5+ page

Font styles to use
Sans Serif

Colors
add136
9bcb3c
606060
474747
ffc214
cadf82
fbee3e
876aae
6b449b

Requirements
Must have
• Pictures of Solar, Wind and power Factor Correction units
Nice to have
• e-commerce platform so contract terms can be purchased through website
Should not have
• Heavy construction equipment

```html
<!DOCTYPE html>
<html lang="en">
<head>
<meta charset="utf-8">
<title>Tidal Forge – Renewable Crypto Mining</title>
<link href="https://fonts.googleapis.com/css2?family=Roboto+Condensed:wght@300;400;700&display=swap" rel="stylesheet">
<style>
:root{
  --green-deep:#14963f;
  --green-mid:#3fa54a;
  --green-soft:#5fb663;
  --green-lime:#9bcb3c;
  --green-bright:#add136;
  --green-pale:#cadf82;
  --yellow:#ffc214;
  --yellow-bright:#fbee3e;
  --yellow-pale:#fde7a6;
  --grey-dark:#474747;
  --grey:#606060;
  --grey-mid:#8f8f8f;
  --navy:#23237e;
  --backdrop:#eeeeee;
  --white:#ffffff;
}
*{box-sizing:border-box;margin:0;padding:0}
html,body{width:1200px;height:1200px;overflow:hidden}
body{background:var(--backdrop);font-family:"Roboto Condensed",Arial,sans-serif;position:relative;color:var(--grey)}
.page{position:absolute;left:454px;top:39px;width:289px;height:1123px;background:var(--white);box-shadow:0 4px 14px rgba(0,0,0,.18);overflow:hidden}
.abs{position:absolute}
/* nav */
.topline{left:0;top:0;width:100%;height:2px;background:var(--green-deep)}
.nav{left:0;top:2px;width:100%;height:16px;background:var(--white);display:flex;justify-content:flex-end;gap:9px;padding-right:43px;align-items:center}
.nav a{font-size:3.2px;color:var(--grey);text-decoration:none;letter-spacing:.1px;text-transform:uppercase;padding:3px 2px}
.nav a.active{background:var(--yellow);color:var(--white);height:12px;display:flex;align-items:center;margin-top:-2px}
/* hero */
.hero{left:0;top:18px;width:100%;height:215px;background:
  radial-gradient(circle at 34% 34%,#5faa3a 0%,#74b944 18%,rgba(140,200,80,.0) 34%),
  radial-gradient(ellipse 120% 40% at 50% 92%,#7cc23e 0%,rgba(160,210,90,.6) 40%,rgba(220,240,190,0) 70%),
  linear-gradient(180deg,#b7de6a 0%,#c9e68a 40%,#e4f2c4 75%,#f2f8e6 100%)}
.brand{display:flex;align-items:center;gap:2px;font-weight:700;color:var(--green-deep);font-size:7px}
.brand .dot{width:7px;height:7px;border-radius:50%;background:var(--green-deep)}
.hero-brand{left:50px;top:15px;background:var(--white);padding:3px 4px;border-radius:1px}
.hero-title{right:48px;top:32px;text-align:right;font-size:18.5px;line-height:20px;color:var(--grey-dark);font-weight:400;letter-spacing:-.3px}
.btn-dark{left:178px;top:96px;width:49px;height:10px;background:var(--grey-dark);color:var(--white);font-size:5px;display:flex;align-items:center;justify-content:center;border-radius:1px}
.login{left:38px;top:117px;width:46px;height:84px;background:var(--yellow);border-radius:4px;box-shadow:0 2px 4px rgba(0,0,0,.2)}
.login .seal{position:absolute;left:12px;top:2px;width:22px;height:22px;border-radius:50%;background:var(--green-mid);border:2px solid var(--white)}
.login .field{position:absolute;left:5px;width:36px;height:5px;background:var(--white);border-radius:2px;font-size:2.5px;color:#bbb;padding-left:6px;line-height:5px}
.login .remember{position:absolute;left:11px;top:57px;font-size:2.2px;color:var(--white)}
.login .go{position:absolute;left:12px;top:66px;width:22px;height:5px;border:.5px solid var(--white);border-radius:2px;font-size:2.5px;color:var(--white);text-align:center;line-height:4.5px}
.login .note{position:absolute;left:5px;top:78px;width:36px;font-size:1.8px;color:var(--white);display:flex;justify-content:space-between}
/* features */
.feature{width:53px;top:245px}
.feature .tile{width:53px;height:53px;background:linear-gradient(135deg,var(--green-lime),#86c040);display:flex;align-items:center;justify-content:center}
.feature .tile svg{width:17px;height:17px}
.feature h3{font-weight:300;font-size:5px;line-height:6px;color:var(--green-lime);text-align:center;margin-top:7px}
.feature p{font-size:2.6px;line-height:3.4px;color:var(--grey-dark);text-align:center;margin-top:5px;padding:0 3px}
.btn-line{width:23px;height:5px;border:.5px solid var(--green-lime);font-size:2.5px;text-align:center;line-height:4.5px;color:var(--grey-dark);margin:3px auto 0;border-radius:1px}
/* content bands */
.band{left:0;width:100%}
.band-buy{top:359px;height:137px;background:var(--green-deep)}
.band-why{top:496px;height:137px;background:var(--green-mid)}
.band-about{top:633px;height:136px;background:var(--green-soft)}
.copy{left:42px;width:88px;color:var(--white)}
.copy h2{font-weight:400;font-size:10px;line-height:12px;letter-spacing:-.2px}
.copy .lead{font-size:4.2px;line-height:5px;margin-top:6px;opacity:.95}
.copy .small{font-size:2.5px;line-height:3.3px;margin-top:4px;opacity:.85}
.btn-ghost{width:30px;height:5px;border:.5px solid var(--white);font-size:2.5px;color:var(--white);text-align:center;line-height:4.5px;margin:7px 0 0 54px;border-radius:1px}
.laptop{left:136px;top:406px;width:150px;height:90px;border-radius:3px;background:linear-gradient(180deg,#c3c3c3 0%,#d8d8d8 100%);padding:4px 5px 8px}
.laptop .screen{width:100%;height:100%;background:linear-gradient(160deg,#f2f2f2 0%,#f2f2f2 8%,#9bd35c 9%,#b9e27e 55%,#8fcb4e 100%)}
.laptop .base{position:absolute;left:-4px;bottom:0;width:158px;height:3px;background:#9a9a9a;border-radius:0 0 2px 2px}
.perk{width:45px;height:45px;border-radius:2px;display:flex;flex-direction:column;align-items:center;justify-content:flex-end;padding-bottom:6px;font-size:5.5px;line-height:6px;text-align:center;gap:4px}
.perk svg{width:16px;height:16px}
.perk.lime{background:var(--green-lime);color:var(--white)}
.perk.gold{background:var(--yellow);color:var(--white)}
.perk.sun{background:var(--yellow-bright);color:var(--grey-dark)}
.perk.plain{background:var(--white);color:var(--grey-dark)}
.bulb{left:142px;top:651px;width:102px;height:100px;border-radius:12px;background:radial-gradient(circle at 50% 45%,#b9e37a 0%,#e9f4df 40%,#ffffff 75%)}
/* pricing */
.band-prices{top:771px;height:204px;background:var(--yellow)}
.prices-title{left:0;top:781px;width:100%;text-align:center;font-size:9px;font-weight:400;color:var(--grey-dark)}
.prices-sub{left:0;top:797px;width:100%;text-align:center;font-size:3.3px;color:var(--grey-dark)}
.table{left:54px;top:811px;width:180px;display:grid;grid-template-columns:repeat(4,45px)}
.plan{height:35px;text-align:center;color:var(--white);margin-right:1px;position:relative}
.plan .name{height:11px;font-size:5px;line-height:11px;font-weight:300}
.plan .price{font-size:9px;line-height:14px;font-weight:300}
.plan .per{font-size:2px;line-height:3px}
.plan.tarif{background:var(--yellow-bright);color:var(--grey-dark)}
.plan.tarif .name{color:var(--yellow)}
.plan.tarif .price{font-size:4px;line-height:14px}
.plan.start{background:var(--green-lime)}
.plan.start .name{background:var(--green-pale);color:var(--white)}
.plan.mid{background:var(--grey-mid)}
.plan.mid .name{background:var(--grey-dark)}
.plan.premium{background:var(--navy)}
.plan.premium .name{background:#3434a6}
.rows{left:54px;top:851px;width:180px}
.row{display:grid;grid-template-columns:repeat(4,45px);height:12px}
.row div{margin-right:1px;font-size:2.5px;color:#b49a5c;display:flex;align-items:center;justify-content:center}
.row div:first-child{justify-content:flex-start;padding-left:4px;color:var(--grey-dark)}
.row:nth-child(odd) div{background:var(--white)}
.row:nth-child(even) div{background:var(--yellow-pale)}
.tick,.cross{width:4px;height:4px}
/* footer */
.band-footer{top:982px;height:91px;background:var(--grey-dark)}
.footer-shade{left:150px;top:1025px;width:139px;height:48px;background:linear-gradient(180deg,rgba(82,82,82,0) 0%,rgba(82,82,82,.7) 100%)}
.foot-h{font-size:5.5px;color:var(--yellow);font-weight:300}
.foot-p{font-size:2.7px;line-height:3.6px;color:var(--white);margin-top:4px}
.btn-gold{width:37px;height:6px;border:.5px solid var(--yellow);font-size:2.5px;color:var(--yellow);text-align:center;line-height:5.5px;border-radius:1px}
.social{display:grid;grid-template-columns:repeat(3,6px);gap:3px 3px}
.social span{width:6px;height:6px;border-radius:50%;border:.5px solid var(--white)}
.foot-links{font-size:2.7px;line-height:8px;color:var(--white);text-transform:uppercase}
.band-bottom{top:1073px;height:50px;background:var(--green-deep)}
.foot-brand{left:48px;top:1085px;color:var(--white);font-size:6px;font-weight:700;display:flex;align-items:center;gap:2px}
.foot-brand .dot{width:6px;height:6px;border-radius:50%;background:var(--white)}
.cards{left:103px;top:1089px;display:flex;gap:3px}
.cards span{width:9px;height:5px;border-radius:1px;background:var(--white);opacity:.85}
.pay-note{left:100px;top:1100px;font-size:2.8px;color:var(--white)}
.addr{font-size:2.6px;line-height:3.5px;color:var(--white)}
</style>
</head>
<body>
<main class="page">
  <div class="abs topline"></div>
  <nav class="abs nav">
    <a>Home</a><a class="active">Pricing</a><a>Our Offer</a><a>About Us</a><a>Customer Service</a>
  </nav>

  <section>
    <div class="abs hero" role="img" aria-label="Green earth globe on flowing green light waves with a white power plug"></div>
    <div class="abs hero-brand brand"><span class="dot"></span>Tidal Forge</div>
    <h1 class="abs hero-title">START<br>TIDAL FORGE<br>TODAY!</h1>
    <div class="abs btn-dark">Learn More</div>
    <form class="abs login">
      <div class="seal"></div>
      <div class="field" style="top:30px">Username</div>
      <div class="field" style="top:40px">Password</div>
      <div class="remember">Remember me</div>
      <div class="go">LOG IN</div>
      <div class="note"><span>Forgot password?</span><span>Register</span></div>
    </form>
  </section>

  <section>
    <div class="abs feature" style="left:54px">
      <div class="tile">
        <svg viewBox="0 0 17 17" fill="none" stroke="#fff" stroke-width=".7" aria-label="Wind turbine icon" role="img"><circle cx="8.5" cy="7" r="1"/><path d="M8.5 6V1.5M9.4 7.5l4 2.3M7.6 7.5l-4 2.3M8.5 8v7.5M6.5 15.5h4"/></svg>
      </div>
      <h3>WIND POWER<br>INVESTMENT</h3>
      <p>Own rigs running on wind. Clean hash rate, steady returns, fully hosted hardware ready for you today.</p>
      <div class="btn-line">Learn More</div>
    </div>
    <div class="abs feature" style="left:118px">
      <div class="tile">
        <svg viewBox="0 0 17 17" fill="none" stroke="#fff" stroke-width=".7" aria-label="Solar panel icon" role="img"><path d="M3 4h11l1.5 6h-14z"/><path d="M8.5 4v6M2.2 7h12.6M5.8 4l-.6 6M11.2 4l.6 6M8.5 10v5M6 15h5"/></svg>
      </div>
      <h3>SOLAR POWER<br>INVESTMENT</h3>
      <p>Own rigs running on sunlight. Clean hash rate, steady returns, fully hosted hardware ready for you today.</p>
      <div class="btn-line">Learn More</div>
    </div>
    <div class="abs feature" style="left:182px">
      <div class="tile">
        <svg viewBox="0 0 17 17" fill="none" stroke="#fff" stroke-width=".7" aria-label="Wallet icon" role="img"><rect x="2" y="5" width="13" height="9" rx="1"/><path d="M3.5 5l7-3 1.2 3"/><rect x="11" y="8" width="4" height="3"/><circle cx="12.5" cy="9.5" r=".4"/></svg>
      </div>
      <h3>GET YOUR FIRST<br>PAYOUT TODAY</h3>
      <p>Pick a term, start mining at once and watch your first payout land in your wallet within the day.</p>
      <div class="btn-line">Learn More</div>
    </div>
  </section>

  <section class="abs band band-buy"></section>
  <div class="abs copy" style="top:373px">
    <h2>Buy And Sell<br>Crypto Currency Miner</h2>
    <p class="lead">Buy mining rigs hosted on a clean grid and sell your terms whenever you like.</p>
    <p class="small">Rigs are housed turnkey in our renewable sites. Choose one, two or three year terms of hash rate and follow output live from your account panel.</p>
    <p class="small">Cooling, power factor correction and upkeep are handled for you, so every rig you own keeps mining at full rate on wind and solar energy.</p>
    <div class="btn-ghost">Learn More</div>
  </div>
  <div class="abs laptop" role="img" aria-label="Laptop showing the Tidal Forge home page">
    <div class="screen"></div>
    <div class="base"></div>
  </div>

  <section class="abs band band-why"></section>
  <div class="abs copy" style="top:519px">
    <h2>Why Choose Tidal Forge?</h2>
    <p class="lead">Clean power, safe hosting and clear terms for every mining investor.</p>
    <p class="small">Our sites run on wind and solar power, with audited uptime and open reporting on every rig and every term you hold.</p>
    <p class="small">Payouts go straight to your wallet, your hardware is insured, and our app lets you check output and earnings anywhere.</p>
    <div class="btn-ghost">Learn More</div>
  </div>
  <div class="abs perk lime" style="left:141px;top:515px">
    <svg viewBox="0 0 16 16" fill="none" stroke="#fff" stroke-width="1"><path d="M8 1.5l5.5 2v4.5c0 3.5-2.5 5.5-5.5 6.5-3-1-5.5-3-5.5-6.5V3.5z"/><rect x="6" y="7" width="4" height="3.5"/><path d="M6.8 7V5.8a1.2 1.2 0 0 1 2.4 0V7"/></svg>
    Safe And Secure</div>
  <div class="abs perk gold" style="left:196px;top:515px">
    <svg viewBox="0 0 16 16" fill="none" stroke="#fff" stroke-width="1"><rect x="4" y="1.5" width="7" height="13" rx="1"/><circle cx="7.5" cy="12.5" r=".6"/><circle cx="12" cy="8" r="2"/></svg>
    Mobile App</div>
  <div class="abs perk sun" style="left:141px;top:567px">
    <svg viewBox="0 0 16 16" fill="none" stroke="#474747" stroke-width="1"><rect x="2" y="4.5" width="12" height="9" rx="1"/><path d="M3 4.5l8-3 1 3"/><rect x="10" y="7.5" width="4" height="3"/></svg>
    Secure Wallet</div>
  <div class="abs perk plain" style="left:196px;top:567px">
    <svg viewBox="0 0 16 16" fill="none" stroke="#474747" stroke-width="1"><rect x="3" y="1.5" width="8" height="12"/><path d="M5 4h4M5 6h4M5 8h2"/><circle cx="11" cy="11" r="3"/><path d="M9.8 11l.8.8 1.6-1.6"/></svg>
    Covered By<br>Insurance</div>

  <section class="abs band band-about"></section>
  <div class="abs copy" style="top:654px">
    <h2>About Tidal Forge?</h2>
    <p class="lead">We build and host mining rigs powered by renewable energy.</p>
    <p class="small">Started by miners and engineers, we run rigs on wind and solar sites fitted with power factor correction to cut waste.</p>
    <p class="small">Investors buy rigs or cloud terms, we keep them running, and the coins mined flow back to each owner every single day.</p>
    <div class="btn-ghost">Learn More</div>
  </div>
  <div class="abs bulb" role="img" aria-label="Light bulb with a young green plant growing inside"></div>

  <section class="abs band band-prices"></section>
  <h2 class="abs prices-title">Prices</h2>
  <p class="abs prices-sub">Pick a hosted mining term of one, two or three years and start earning from clean energy.</p>
  <div class="abs table">
    <div class="plan tarif"><div class="name">TARIF</div><div class="price">PRICING TABLE</div><div class="per">compare plans</div></div>
    <div class="plan start"><div class="name">START</div><div class="price">$29.99</div><div class="per">per month</div></div>
    <div class="plan mid"><div class="name">&nbsp;</div><div class="price">$49.99</div><div class="per">per month</div></div>
    <div class="plan premium"><div class="name">PREMIUM</div><div class="price">$69.99</div><div class="per">per month</div></div>
  </div>
  <div class="abs rows">
    <div class="row"><div>Hosted rig</div><div><svg class="cross" viewBox="0 0 4 4" stroke="#474747" stroke-width=".5"><path d="M.5.5l3 3M3.5.5l-3 3"/></svg></div><div><svg class="tick" viewBox="0 0 4 4" fill="none" stroke="#474747" stroke-width=".5"><path d="M.5 2l1 1 2-2.5"/></svg></div><div><svg class="tick" viewBox="0 0 4 4" fill="none" stroke="#474747" stroke-width=".5"><path d="M.5 2l1 1 2-2.5"/></svg></div></div>
    <div class="row"><div>Storage space</div><div>4 GB</div><div>16 GB</div><div>UNLIMITED</div></div>
    <div class="row"><div>Contacts</div><div>15 CONTACTS</div><div>30 CONTACTS</div><div>&gt;50 CONTACTS</div></div>
    <div class="row"><div>Daily payout</div><div><svg class="tick" viewBox="0 0 4 4" fill="none" stroke="#474747" stroke-width=".5"><path d="M.5 2l1 1 2-2.5"/></svg></div><div><svg class="tick" viewBox="0 0 4 4" fill="none" stroke="#474747" stroke-width=".5"><path d="M.5 2l1 1 2-2.5"/></svg></div><div><svg class="tick" viewBox="0 0 4 4" fill="none" stroke="#474747" stroke-width=".5"><path d="M.5 2l1 1 2-2.5"/></svg></div></div>
    <div class="row"><div>Live stats</div><div><svg class="cross" viewBox="0 0 4 4" stroke="#474747" stroke-width=".5"><path d="M.5.5l3 3M3.5.5l-3 3"/></svg></div><div><svg class="cross" viewBox="0 0 4 4" stroke="#474747" stroke-width=".5"><path d="M.5.5l3 3M3.5.5l-3 3"/></svg></div><div><svg class="tick" viewBox="0 0 4 4" fill="none" stroke="#474747" stroke-width=".5"><path d="M.5 2l1 1 2-2.5"/></svg></div></div>
    <div class="row"><div>Green energy</div><div><svg class="tick" viewBox="0 0 4 4" fill="none" stroke="#474747" stroke-width=".5"><path d="M.5 2l1 1 2-2.5"/></svg></div><div><svg class="tick" viewBox="0 0 4 4" fill="none" stroke="#474747" stroke-width=".5"><path d="M.5 2l1 1 2-2.5"/></svg></div><div><svg class="tick" viewBox="0 0 4 4" fill="none" stroke="#474747" stroke-width=".5"><path d="M.5 2l1 1 2-2.5"/></svg></div></div>
    <div class="row"><div>Support team</div><div>1 PERSON</div><div>4 PERSON</div><div>&gt;10 PERSON</div></div>
    <div class="row"><div>Insurance</div><div><svg class="cross" viewBox="0 0 4 4" stroke="#474747" stroke-width=".5"><path d="M.5.5l3 3M3.5.5l-3 3"/></svg></div><div><svg class="tick" viewBox="0 0 4 4" fill="none" stroke="#474747" stroke-width=".5"><path d="M.5 2l1 1 2-2.5"/></svg></div><div><svg class="tick" viewBox="0 0 4 4" fill="none" stroke="#474747" stroke-width=".5"><path d="M.5 2l1 1 2-2.5"/></svg></div></div>
    <div class="row"><div>Mobile app</div><div><svg class="tick" viewBox="0 0 4 4" fill="none" stroke="#474747" stroke-width=".5"><path d="M.5 2l1 1 2-2.5"/></svg></div><div><svg class="tick" viewBox="0 0 4 4" fill="none" stroke="#474747" stroke-width=".5"><path d="M.5 2l1 1 2-2.5"/></svg></div><div><svg class="tick" viewBox="0 0 4 4" fill="none" stroke="#474747" stroke-width=".5"><path d="M.5 2l1 1 2-2.5"/></svg></div></div>
    <div class="row"><div>Backups</div><div>4 GB</div><div>16 GB</div><div>UNLIMITED</div></div>
  </div>

  <footer>
    <div class="abs band band-footer"></div>
    <div class="abs footer-shade" role="img" aria-label="Faint city outline in the footer background"></div>
    <div class="abs" style="left:46px;top:996px;width:46px">
      <div class="foot-h">Member Area</div>
      <p class="foot-p">If you don't have an account, sign up for free.</p>
      <div class="btn-gold" style="margin-top:7px">SIGN UP</div>
      <div class="btn-gold" style="margin-top:8px">LOG IN</div>
    </div>
    <div class="abs" style="left:104px;top:996px;width:40px">
      <div class="foot-h">Follow us</div>
      <p class="foot-p">Stay up to date with Tidal Forge activities.</p>
      <div class="social" style="margin-top:11px"><span></span><span></span><span></span><span></span><span></span><span></span></div>
    </div>
    <div class="abs foot-links" style="left:156px;top:1017px">Home<br>Pricing<br>Our Offer</div>
    <div class="abs foot-links" style="left:188px;top:1017px">About Us<br>Datacenter<br>Press</div>
    <div class="abs foot-links" style="left:222px;top:1017px">Privacy<br>Contact</div>

    <div class="abs band band-bottom"></div>
    <div class="abs foot-brand"><span class="dot"></span>Tidal Forge</div>
    <div class="abs cards"><span></span><span></span><span></span></div>
    <p class="abs pay-note">No account, card payment</p>
    <p class="abs addr" style="left:154px;top:1088px">Address<br>Tidal Forge<br><br>12 Harbour Lane<br>Unit 4, North Quay<br>Port Alder 3041</p>
    <p class="abs addr" style="left:205px;top:1088px">Address<br>Tidal Forge<br><br>88 Windmill Road<br>Block B, Solar Park<br>Fernvale 2210</p>
  </footer>
</main>
</body>
</html>
```